Thornvale Agribusiness Consulting needs a Website Design.

We need a website design for a new company based in UK. Thornvale offers agribusiness consulting and farm design services to farmers, smallholders and the wider agribusiness industry to assist clients in adopting more sustainable and regenerative production, processing and marketing practices.
Services are offered face-to-face and on a remote platform.
Services are offered in the UK and overseas.
We would like to see designs that reflect the natural environment, business and sustainability. Desired colours; green, blue, grey. The final design should communicate professionalism in the rural economy.
The design should be able to be customized by the client to make future changes and additions.
Target Market(s)
Farmers, smallholders, and the agricultural industry in UK and overseas.
Industry/Entity Type
Agribusiness
Number of Pages Required
4 page
Look and feel
Each slider illustrates characteristics of the customer's brand and the style your logo design should communicate.

```html
<!DOCTYPE html>
<html lang="en">
<head>
<meta charset="utf-8">
<title>Thornvale Agribusiness Consulting</title>
<link rel="stylesheet" href="https://fonts.googleapis.com/css2?family=Bitter:wght@400;700&family=Open+Sans:wght@400;600&display=swap">
<style>
:root{
  --green:#8cc63f;
  --green-dark:#7ab52f;
  --teal:#16997a;
  --blue:#1878c0;
  --ink:#222;
  --text:#444;
  --muted:#666;
  --line:#e2e2e2;
  --footer:#333;
  --white:#fff;
}
*{margin:0;padding:0;box-sizing:border-box}
html,body{width:800px;height:1200px;overflow:hidden;background:var(--white)}
body{position:relative;font-family:"Open Sans",Arial,sans-serif;color:var(--text)}
.abs{position:absolute}
.serif{font-family:"Bitter",Georgia,serif}

.top-rule{left:0;top:0;width:800px;height:2px;background:var(--green)}
.logo{left:66px;top:26px;font:700 21px "Bitter",Georgia,serif;color:var(--ink);letter-spacing:.5px}
.nav a{position:absolute;top:34px;font:400 11px "Bitter",Georgia,serif;color:var(--ink);text-decoration:none;letter-spacing:.3px}
.nav a.active{color:var(--green)}
.nav-underline{left:257px;top:67px;width:45px;height:3px;background:var(--green)}

.hero{left:0;top:70px;width:800px;height:300px}
.hero-kicker{left:82px;top:120px;font:400 19px "Bitter",Georgia,serif;color:var(--white)}
.hero-title{left:77px;top:138px;font:400 40px "Bitter",Georgia,serif;color:var(--white)}
.hero-copy{left:79px;top:193px;width:200px;font-size:8px;line-height:14px;color:var(--white)}
.hero-btn{left:80px;top:240px;width:86px;height:33px;background:#1c1c1c;border-radius:2px;color:var(--white);font:400 11px "Bitter",Georgia,serif;display:flex;align-items:center;justify-content:center}
.dot{top:288px;width:7px;height:7px;border-radius:50%;background:#ddd}
.dot.on{background:#111}

.section-title{font:400 21px "Bitter",Georgia,serif;color:var(--ink);letter-spacing:.3px}
.wwd-title{left:0;width:800px;top:331px;text-align:center}

.card{top:414px;width:214px;height:172px;color:var(--white);text-align:center}
.card::after{content:"";position:absolute;left:30px;right:30px;bottom:-6px;height:6px;border-radius:50%;background:rgba(0,0,0,.08)}
.card.consult{left:66px;background:var(--green)}
.card.produce{left:293px;background:var(--teal)}
.card.market{left:520px;background:var(--blue)}
.card-badge{position:absolute;left:57px;top:-47px;width:100px;height:100px;border-radius:50%;background:var(--white);display:flex;align-items:center;justify-content:center}
.card-badge span{width:84px;height:84px;border-radius:50%;display:flex;align-items:center;justify-content:center}
.consult .card-badge span{background:var(--green)}
.produce .card-badge span{background:var(--teal)}
.market .card-badge span{background:var(--blue)}
.card h3{position:absolute;left:0;right:0;top:66px;font:400 22px "Bitter",Georgia,serif;letter-spacing:.5px}
.card p{position:absolute;left:14px;right:14px;top:104px;font-size:8.5px;line-height:13.6px}

.services{left:0;top:625px;width:800px;height:249px;background:linear-gradient(#fff,#ececec);border-top:1px solid var(--line);border-bottom:1px solid #e6e6e6}
.svc-title{left:65px;top:656px}
.arrows{font:400 16px "Bitter",Georgia,serif;color:var(--ink);letter-spacing:6px}
.tile{top:700px;width:164px;height:133px}
.tile-feature{left:66px;background:linear-gradient(135deg,#8cc63f,#9ccd55);color:var(--white);padding:16px 12px}
.tile-feature h4{font:400 17px "Bitter",Georgia,serif;line-height:21px;text-shadow:0 1px 1px rgba(0,0,0,.2)}
.tile-feature p{margin-top:10px;font-size:8px;line-height:13.6px}

.welcome-title{left:64px;top:910px;font:400 21px "Bitter",Georgia,serif;color:var(--ink)}
.share{left:373px;top:921px;width:46px;height:11px;display:flex;gap:2px}
.share i{display:block;height:11px;border:1px solid #bbb;border-radius:2px;background:#eef1f5}
.welcome-copy{left:66px;width:356px;font-size:8px;line-height:13.6px;color:var(--text)}
.btn-green{left:66px;top:1054px;width:76px;height:36px;background:var(--green);border-radius:2px;color:var(--white);font:400 11px "Bitter",Georgia,serif;display:flex;align-items:center;justify-content:center}

.news{left:441px;top:916px;width:295px;height:174px;border:1px solid #ddd;background:linear-gradient(#fff,#f0f0f0)}
.news-title{left:463px;top:937px;font:400 21px "Bitter",Georgia,serif;color:var(--ink)}
.news-arrows{left:697px;top:937px}
.news-img{left:465px;top:983px;width:110px;height:87px}
.news-head{left:587px;top:983px;font:700 10px "Open Sans",Arial,sans-serif;color:var(--green);letter-spacing:.2px}
.news-date{left:588px;top:1002px;font-size:7.5px;color:var(--ink)}
.news-copy{left:587px;top:1020px;width:122px;font-size:8px;line-height:10.5px;color:var(--ink)}
.news-more{left:588px;top:1062px;font-size:7.5px;color:var(--green)}

.footer{left:0;top:1133px;width:800px;height:67px;background:var(--footer)}
.footer-nav a{position:absolute;top:1155px;font:400 8px "Bitter",Georgia,serif;color:#bbb;text-decoration:none;letter-spacing:.3px}
.copyright{left:67px;top:1172px;font:400 7px "Bitter",Georgia,serif;color:#bbb}
.social{top:1159px;width:13px;height:13px;border-radius:2px}
</style>
</head>
<body>

<div class="abs top-rule"></div>
<div class="abs logo">THORNVALE</div>
<nav class="nav">
  <a class="active" style="left:264px">HOME</a>
  <a style="left:326px">ABOUT US</a>
  <a style="left:411px">PROJECTS</a>
  <a style="left:490px">WHAT WE DO</a>
  <a style="left:591px">SERVICES</a>
  <a style="left:669px">CONTACT US</a>
</nav>
<div class="abs nav-underline"></div>

<svg class="abs hero" viewBox="0 0 800 300" role="img" aria-label="Photo of a large oak tree in a green field under a stormy sky">
  <defs>
    <linearGradient id="sky" x1="0" y1="0" x2="0" y2="1">
      <stop offset="0" stop-color="#8d949b"/>
      <stop offset=".55" stop-color="#5e6b78"/>
      <stop offset=".72" stop-color="#3d5a2e"/>
      <stop offset="1" stop-color="#6f9a3a"/>
    </linearGradient>
  </defs>
  <rect width="800" height="300" fill="url(#sky)"/>
  <rect x="66" y="0" width="223" height="300" fill="#8cc63f" opacity=".92"/>
  <path d="M0 298 C150 250 280 236 400 236 C520 236 650 250 800 298 L800 300 L0 300 Z" fill="#fff"/>
</svg>
<div class="abs hero-kicker">Agri Business</div>
<div class="abs hero-title">Consulting</div>
<p class="abs hero-copy">Neque porro quisquam est, qui dolorem ipsum quia dolor sit amet, consectetur.</p>
<div class="abs hero-btn">READ MORE</div>
<span class="abs dot on" style="left:83px"></span>
<span class="abs dot" style="left:96px"></span>
<span class="abs dot" style="left:110px"></span>

<h2 class="abs section-title wwd-title">WHAT WE DO</h2>

<div class="abs card consult">
  <div class="card-badge"><span>
    <svg width="40" height="40" viewBox="0 0 40 40" fill="#fff"><circle cx="26" cy="8" r="4"/><path d="M22 14h8l2 14h-6l-6-6z"/><path d="M4 30h32v4H4z"/><path d="M10 22l2 8h-4z M16 20l2 10h-4z"/></svg>
  </span></div>
  <h3>CONSULTING</h3>
  <p>providing management, technical and networking (@ThornvaleFarmers) services to smallholders, farmers and the agribusiness</p>
</div>
<div class="abs card produce">
  <div class="card-badge"><span>
    <svg width="40" height="40" viewBox="0 0 40 40" fill="none" stroke="#fff" stroke-width="3"><circle cx="11" cy="28" r="6"/><circle cx="30" cy="30" r="4"/><path d="M8 20V10h12l4 10h10v8" stroke-linejoin="round"/></svg>
  </span></div>
  <h3>PRODUCTION</h3>
  <p>establishing a "Farm of the Future" production base to showcase regenerative and biologically intensive production methods.</p>
</div>
<div class="abs card market">
  <div class="card-badge"><span>
    <svg width="40" height="40" viewBox="0 0 40 40" fill="#fff"><circle cx="26" cy="7" r="4"/><path d="M22 13h7v22h-4V22l-5-3z"/><path d="M8 6l12 14" stroke="#fff" stroke-width="2"/><path d="M6 32h14v3H6z M10 26l2 6h-4z"/></svg>
  </span></div>
  <h3>MARKETING</h3>
  <p>developing knowledge and markets in local schools and communities via the "Our Local Farm" program</p>
</div>

<section class="abs services"></section>
<h2 class="abs section-title svc-title">OUR SERVICES</h2>
<div class="abs arrows" style="left:708px;top:657px">‹ ›</div>
<div class="abs tile tile-feature">
  <h4>FARM DESIGN &amp; PLANNING</h4>
  <p>Regenerative agriculture planning and design: onsite and remotely...</p>
</div>
<div class="abs tile" style="left:234px;background:linear-gradient(#8a9099,#6f8a4a 45%,#5d7a33)" role="img" aria-label="Photo of a wooden farm gate in a field"></div>
<div class="abs tile" style="left:402px;background:radial-gradient(circle at 60% 45%,#f3f3f3,#d6d6d6 70%,#bdbdbd)" role="img" aria-label="Photo of white and brown eggs in a tray"></div>
<div class="abs tile" style="left:570px;background:linear-gradient(135deg,#4f7a32,#c6472f 45%,#d9b35c 75%,#3b3b3b)" role="img" aria-label="Photo of locally grown vegetables at a market stall"></div>

<h2 class="abs welcome-title">WELCOME TO THORNVALE</h2>
<div class="abs share"><i style="width:33px"></i><i style="width:11px"></i></div>
<p class="abs welcome-copy" style="top:946px">Martin has over 25 years professional experience working in the agricultural industry in the UK and overseas. Beginning his career with not-for-profit organisations in Asia and Africa, Martin assisted rural communities rehabilitate and develop their farm businesses and local economies with large scale sustainable agricultural programs.</p>
<p class="abs welcome-copy" style="top:1014px">Martin established Thornvale and continues to undertake consulting assignments in Asia, Australia and South Africa assisting</p>
<div class="abs btn-green">Read More</div>

<div class="abs news"></div>
<h2 class="abs news-title">LATEST NEWS</h2>
<div class="abs arrows news-arrows">‹ ›</div>
<div class="abs news-img" style="background:linear-gradient(#caa463,#b58a48)" role="img" aria-label="Photo of round hay bales in a harvested field"></div>
<div class="abs news-head">LOREM IPSUM DOLOR</div>
<div class="abs news-date">MAY 02,2015</div>
<p class="abs news-copy">Neque porro quisquam est, qui dolorem ipsum quia dolor sit amet, consectetur...</p>
<div class="abs news-more">Read More</div>

<footer class="abs footer"></footer>
<nav class="footer-nav">
  <a style="left:66px">HOME</a>
  <a style="left:114px">ABOUT US</a>
  <a style="left:178px">SERVICES</a>
  <a style="left:241px">CLIENTS</a>
  <a style="left:298px">CONTACT US</a>
</nav>
<div class="abs copyright">© 2015 THORNVALE. ALL RIGHTS RESERVED.</div>
<span class="abs social" style="left:682px;background:#3b5b98"></span>
<span class="abs social" style="left:701px;background:#2aa9e0"></span>
<span class="abs social" style="left:720px;background:#f47b20"></span>

</body>
</html>
```